Cat-products company needs smart, yet endearing, business card

We need a business card design for a new, but up-and-running, business based in Honolulu, Hawaii. The business is Purrnest Nook Co. Our first product is the most environmentally-friendly cat grass kit ever seen on the planet. Future products, currently in the R&D phase, will include a variety of exciting cat scratchers. We also do consulting work to help apartment-dwellers make their home more cat-friendly and, in the future, plan on doing full, custom installs of structure to create high walkways for cats.

Target Market(s)

Middle-aged, apartment-dwelling, middle-class workers who own 1 or more cats and who dote on them.

Industry/Entity Type

Pet Care

Contact Information for Business Card

A striking, professional, yet warm and friendly design is what we're after.

Font styles to use
Serif
Sans Serif
Other font styles liked:
• Comfortaa

Colors

Designer to choose colors to be used in the design.

Requirements
Must have
• The company logo: (see attachment)
• The company name: Purrnest Nook Co
• The web address: www.purrnestnookco.com
• Email: support@purrnestnookco.com
• Phone: +1 (808) 571 6023
• Update (Fri Jun 30 3017 7:45pm Hawaii Time) I would like, is possible, uploaded picture of the cat grass kit on the back of the card with some text along the lines of: Purrnest Nook Co - Maker Of The Leafiest Feline Sprout Set Yet
Nice to have
• A cat picture, cartoon, real or silhouette that illustrates cats in action and/or relaxing; ie using the apartment space to live, play and relax in and being well-contented.
• Most of the website is done in the font: Comfortaa. It might be nice to continue using this for brand consistency.
Should not have
• Hard-to-read fonts.

```html
<!DOCTYPE html>
<html lang="en">
<head>
<meta charset="utf-8">
<title>Purrnest Nook Co – Business Card</title>
<link rel="stylesheet" href="https://fonts.googleapis.com/css2?family=Comfortaa:wght@700&family=Roboto:wght@400&family=Roboto+Condensed:wght@700&display=swap">
<style>
  :root {
    --backdrop: #e3e3e3;
    --card-light: #f7f7f6;
    --card-dark: #52312b;
    --brand-brown: #52312b;
    --brand-gold: #f0ac0f;
    --text-grey: #4b4b4b;
    --rule: #cfcfcf;
    --social-dot: #8a6a60;
    --white: #ffffff;
    --tagline: #e9dcd6;
  }
  * { box-sizing: border-box; margin: 0; padding: 0; }
  html, body {
    width: 1200px; height: 960px; overflow: hidden;
    background: var(--backdrop);
  }
  .card {
    position: absolute;
    width: 600px; height: 342px;
  }
  .card--front { left: 314px; top: 113px; background: var(--card-light); }
  .card--back { left: 311px; top: 472px; background: var(--card-dark); }

  .brand-mark {
    position: absolute;
    display: flex; flex-direction: column; align-items: center;
    font-family: "Comfortaa", sans-serif; font-weight: 700;
    text-align: center;
  }
  .brand-mark__dot { border-radius: 50%; margin-bottom: 14px; }
  .card--front .brand-mark { left: 63px; top: 80px; width: 200px; }
  .card--front .brand-mark__dot { width: 72px; height: 72px; background: var(--brand-brown); }
  .card--front .brand-mark__name { color: var(--brand-brown); font-size: 26px; line-height: 1.2; }

  .divider {
    position: absolute; left: 293px; top: 78px;
    width: 1px; height: 192px; background: var(--rule);
  }

  .contact { position: absolute; left: 333px; top: 88px; font-family: "Roboto", sans-serif; }
  .contact__name {
    font-family: "Roboto Condensed", sans-serif; font-weight: 700;
    font-size: 21px; color: var(--brand-brown); letter-spacing: 0.2px; line-height: 24px;
  }
  .contact__role {
    font-family: "Roboto Condensed", sans-serif; font-weight: 700;
    font-size: 15px; color: var(--brand-gold); line-height: 20px; margin-top: 2px;
  }
  .contact__address { margin-top: 16px; font-size: 14px; line-height: 18px; color: var(--text-grey); }
  .contact__list { list-style: none; margin-top: 10px; }
  .contact__item {
    display: flex; align-items: center; gap: 8px;
    font-size: 14px; line-height: 19.5px; color: var(--text-grey);
  }
  .contact__icon { width: 13px; height: 13px; fill: var(--brand-brown); flex: none; }

  .social { position: absolute; right: 17px; top: 19px; display: flex; gap: 2px; }
  .social__dot { width: 22px; height: 22px; border-radius: 50%; background: var(--social-dot); }

  .card--back .brand-mark { left: 0; top: 62px; width: 600px; }
  .card--back .brand-mark__dot { width: 100px; height: 100px; background: var(--white); margin-bottom: 14px; }
  .card--back .brand-mark__name { color: var(--brand-gold); font-size: 34px; line-height: 1.15; }

  .back-tagline {
    position: absolute; left: 0; top: 268px; width: 600px; text-align: center;
    font-family: "Roboto", sans-serif; font-size: 11.5px; letter-spacing: 0.4px; color: var(--tagline);
  }
  .back-url {
    position: absolute; left: 0; top: 294px; width: 600px; text-align: center;
    font-family: "Roboto", sans-serif; font-size: 14px; letter-spacing: 4px; color: var(--white);
  }
</style>
</head>
<body>

<section class="card card--front">
  <div class="brand-mark">
    <span class="brand-mark__dot"></span>
    <span class="brand-mark__name">Purrnest<br>Nook Co</span>
  </div>

  <div class="divider"></div>

  <div class="contact">
    <p class="contact__name">LEILANI KAHALE</p>
    <p class="contact__role">CEO/FOUNDER</p>
    <p class="contact__address">2146 Kaimoku Way<br>Honolulu, Hawaii 96815</p>
    <ul class="contact__list">
      <li class="contact__item">
        <svg class="contact__icon" viewBox="0 0 16 16" aria-hidden="true"><path d="M3.6 1.2l2.3 2.6-1.3 1.8c.9 2 2.6 3.7 4.7 4.7l1.8-1.3 2.6 2.3-1.4 2.3C7.2 13.6 2.4 8.8 1.3 2.6z"/></svg>
        +1 (808) 571 6023
      </li>
      <li class="contact__item">
        <svg class="contact__icon" viewBox="0 0 16 16" aria-hidden="true"><path d="M1 3h14v1.4L8 9 1 4.4z"/><path d="M1 6l7 4.6L15 6v7H1z"/></svg>
        support@purrnestnookco.com
      </li>
      <li class="contact__item">
        <svg class="contact__icon" viewBox="0 0 16 16" aria-hidden="true"><circle cx="8" cy="8" r="7"/><path d="M5 4c1.5 0 2 1 1.6 2S4 7 4.6 8.6 7 9.5 6.6 12M10 3c-.5 1.4.6 2 1.8 2.2M11 9.5c1 .2 1.5 1.2 1.2 2.4" stroke="#f7f7f6" stroke-width="1.2" fill="none"/></svg>
        www.purrnestnookco.com
      </li>
    </ul>
  </div>
</section>

<section class="card card--back">
  <div class="social" aria-label="Social profiles">
    <span class="social__dot"></span>
    <span class="social__dot"></span>
    <span class="social__dot"></span>
    <span class="social__dot"></span>
  </div>

  <div class="brand-mark">
    <span class="brand-mark__dot"></span>
    <span class="brand-mark__name">Purrnest<br>Nook Co</span>
  </div>

  <p class="back-tagline">Purrnest Nook Co - Maker Of The Leafiest Feline Sprout Set Yet</p>
  <p class="back-url">www.purrnestnookco.com</p>
</section>

</body>
</html>
```